Need Business Card for our Real Estate Business with Sales Executive's Picture

PANTONE 484 C ( RED)

PANTONE 2766 C ( BLUE

Industry/Entity Type

Real Estate

Contact Information for Business Card

Name, Mobile, email, & picture of Person
Agency Phone, address, Web address

Requirements
Must have
• Our Logo Colours, Agent Picture,

```html
<!DOCTYPE html>
<html lang="en">
<head>
<meta charset="utf-8">
<title>Meridian Homes – Business Card</title>
<link href="https://fonts.googleapis.com/css2?family=Work+Sans:wght@400;500;600&display=swap" rel="stylesheet">
<style>
  :root {
    --navy: #111c4e;
    --navy-light: #2a3770;
    --red: #8e2b35;
    --white: #ffffff;
    --ink: #1a2350;
    --muted: #5a5f73;
    --backdrop: #4a4540;
  }
  html, body {
    margin: 0;
    padding: 0;
    width: 1200px;
    height: 930px;
    overflow: hidden;
    background: var(--backdrop);
    font-family: "Work Sans", Arial, sans-serif;
  }
  .canvas {
    position: relative;
    width: 1200px;
    height: 930px;
  }
  .card {
    position: absolute;
    left: 230px;
    width: 740px;
    height: 410px;
    border-radius: 18px;
    overflow: hidden;
    box-shadow: 0 10px 24px rgba(0,0,0,0.35);
  }
  .card--back {
    top: 40px;
    background: linear-gradient(135deg, var(--navy) 0%, #18265e 50%, var(--navy) 100%);
    display: flex;
    align-items: center;
    justify-content: center;
  }
  .card--front {
    top: 480px;
    background: var(--white);
  }
  .card__shapes {
    position: absolute;
    inset: 0;
  }
  .brand {
    display: flex;
    align-items: center;
    gap: 12px;
    font-weight: 600;
    letter-spacing: 0.08em;
    text-transform: uppercase;
    white-space: nowrap;
  }
  .brand__mark {
    width: 12px;
    height: 12px;
    flex: none;
  }
  .card--back .brand {
    color: var(--white);
    font-size: 44px;
  }
  .card--back .brand__mark { background: var(--white); width: 14px; height: 14px; }
  .card--front .brand {
    position: absolute;
    left: 48px;
    top: 150px;
    color: var(--ink);
    font-size: 28px;
  }
  .card--front .brand__mark { background: var(--red); }
  .address {
    position: absolute;
    left: 62px;
    top: 205px;
    margin: 0;
    color: var(--muted);
    font-size: 16px;
    line-height: 1.4;
  }
  .photo {
    position: absolute;
    left: 520px;
    top: 16px;
    width: 170px;
    height: 170px;
    border-radius: 50%;
    background: var(--white);
    box-shadow: 0 0 0 3px var(--navy);
    display: flex;
    align-items: center;
    justify-content: center;
  }
  .photo__fill {
    width: 156px;
    height: 156px;
    border-radius: 50%;
    background: linear-gradient(180deg, #c9a58c 0%, #b08a72 40%, #23408f 75%, #1a2f70 100%);
  }
  .contact {
    position: absolute;
    right: 34px;
    top: 218px;
    text-align: right;
    color: var(--white);
  }
  .contact__name {
    font-size: 22px;
    font-weight: 600;
    letter-spacing: 0.02em;
    text-transform: uppercase;
  }
  .contact__role {
    font-size: 15px;
    margin: 2px 0 10px;
  }
  .contact__line {
    display: flex;
    justify-content: flex-end;
    align-items: center;
    gap: 8px;
    font-size: 15px;
    line-height: 1.45;
  }
  .contact__icon {
    width: 12px;
    height: 12px;
    fill: none;
    stroke: var(--white);
    stroke-width: 1.6;
  }
</style>
</head>
<body>
<main class="canvas">

  <section class="card card--back" aria-label="Card back">
    <div class="brand"><span class="brand__mark"></span>Meridian Homes</div>
  </section>

  <section class="card card--front" aria-label="Card front">
    <svg class="card__shapes" viewBox="0 0 740 410" width="740" height="410" aria-hidden="true">
      <defs>
        <linearGradient id="navySweep" x1="0" y1="1" x2="1" y2="0">
          <stop offset="0" stop-color="#2a3770"/>
          <stop offset="0.45" stop-color="#111c4e"/>
          <stop offset="1" stop-color="#111c4e"/>
        </linearGradient>
      </defs>
      <path d="M560,0 C520,180 420,320 0,365 L0,410 L740,410 L740,0 Z" fill="url(#navySweep)"/>
      <path d="M540,175 C470,290 350,360 0,382" fill="none" stroke="#ffffff" stroke-width="14"/>
      <path d="M532,180 C462,292 342,360 0,378" fill="none" stroke="#8e2b35" stroke-width="6"/>
      <path d="M690,78 L740,66" stroke="#ffffff" stroke-width="14"/>
      <path d="M690,72 L740,60" stroke="#8e2b35" stroke-width="6"/>
    </svg>

    <div class="brand"><span class="brand__mark"></span>Meridian Homes</div>
    <p class="address">Via dei Colli, 48.<br>12030 Saluzzo (CN)</p>

    <div class="photo">
      <div class="photo__fill" role="img" aria-label="Portrait photo of the managing director"></div>
    </div>

    <div class="contact">
      <div class="contact__name">Daniel Moretti</div>
      <div class="contact__role">Managing Director</div>
      <div class="contact__line">+852 2100 4417
        <svg class="contact__icon" viewBox="0 0 12 12"><path d="M2 1 L4.5 1 L5.5 3.5 L4 4.5 C4.8 6.2 5.8 7.2 7.5 8 L8.5 6.5 L11 7.5 L11 10 C6 10.5 1.5 6 2 1 Z"/></svg>
      </div>
      <div class="contact__line">+852 2100 4418
        <svg class="contact__icon" viewBox="0 0 12 12"><rect x="3" y="1" width="6" height="10" rx="1"/><path d="M5 9.3 L7 9.3"/></svg>
      </div>
      <div class="contact__line">info@meridianhomes.com
        <svg class="contact__icon" viewBox="0 0 12 12"><rect x="1" y="2.5" width="10" height="7"/><path d="M1 2.5 L6 6.5 L11 2.5"/></svg>
      </div>
      <div class="contact__line">www.meridianhomes.com
        <svg class="contact__icon" viewBox="0 0 12 12"><circle cx="6" cy="6" r="5"/><path d="M1 6 L11 6 M6 1 C3.5 4 3.5 8 6 11 M6 1 C8.5 4 8.5 8 6 11"/></svg>
      </div>
    </div>
  </section>

</main>
</body>
</html>
```